Whitcombe Business Card Design

The name of the business is Dario Whitcombe, CPA LLC
The service that we offer is Accounting, Tax & Consulting Services. I need it to have the following items:
Dario Whitcombe, Principal
Phone Number
Email Address
Physical Address

I have attached the company logo, one in black and one in white. Please provide a design in black background and the other in white background. Please include "Accounting, Tax & Consulting Services". I want the business card to be clean and very professional.

```html
<!DOCTYPE html>
<html lang="en">
<head>
<meta charset="utf-8">
<title>Dario Whitcombe, CPA LLC – Business Cards</title>
<link href="https://fonts.googleapis.com/css2?family=Montserrat:wght@400;500;600;700&display=swap" rel="stylesheet">
<style>
  :root{
    --bg:#d9dadc;
    --card:#ffffff;
    --card-dark:#1d1d1f;
    --red:#9b1b1f;
    --charcoal:#38383a;
    --grey:#8e8e90;
    --light-grey:#b4b4b7;
    --text-grey:#7a7a7d;
    --divider:#8a8a8c;
    --white:#ffffff;
  }
  *{margin:0;padding:0;box-sizing:border-box}
  html,body{width:1200px;height:1000px;overflow:hidden}
  body{background:var(--bg);font-family:'Montserrat',sans-serif;position:relative}

  .card{position:absolute;background:var(--card);box-shadow:4px 5px 8px rgba(0,0,0,.35)}
  .card--contact{left:410px;top:90px;width:722px;height:400px}
  .card--brand{left:88px;top:535px;width:720px;height:402px;background:var(--card-dark)}

  .band{position:absolute;left:0;width:100%;display:flex}
  .band span{flex:1}
  .band--top span{border-radius:0 0 8px 8px}
  .band--bottom span{border-radius:8px 8px 0 0}
  .card--contact .band--top{top:0;height:11px}
  .card--contact .band--bottom{bottom:0;height:17px}
  .card--brand .band--top{top:0;height:16px}
  .card--brand .band--bottom{bottom:0;height:12px}
  .c-red{background:var(--red)}
  .c-dark{background:var(--charcoal)}
  .c-grey{background:var(--grey)}
  .card--brand .c-dark{background:var(--light-grey)}

  .person{position:absolute;left:41px;top:134px}
  .person__name{color:var(--red);font-size:25px;font-weight:500;letter-spacing:.3px;line-height:1}
  .person__name b{font-weight:700}
  .person__role{margin-top:13px;font-size:13px;font-weight:500;letter-spacing:1px;color:var(--charcoal)}

  .contacts{position:absolute;left:42px;top:196px;list-style:none}
  .contacts li{display:flex;align-items:center;gap:3px;height:33px;font-size:16px;font-weight:500;color:var(--text-grey)}
  .contacts svg{width:18px;height:18px;flex:none}

  .divider{position:absolute;left:359px;top:118px;width:3px;height:165px;background:var(--divider)}

  .lockup{position:absolute;text-align:center}
  .card--contact .lockup{left:383px;width:320px;top:146px}
  .card--brand .lockup{left:0;width:100%;top:118px}
  .lockup__mark{display:block;margin:0 auto;background:var(--red)}
  .card--contact .lockup__mark{width:40px;height:40px;margin-bottom:34px}
  .card--brand .lockup__mark{width:60px;height:60px;margin-bottom:44px}
  .lockup__name{color:var(--charcoal);font-weight:500;letter-spacing:.5px;white-space:nowrap;line-height:1.2}
  .card--contact .lockup__name{font-size:17px}
  .card--brand .lockup__name{font-size:26px;color:var(--white)}
  .lockup__tag{color:var(--text-grey);font-weight:600;letter-spacing:1.5px;line-height:1.2}
  .card--contact .lockup__tag{font-size:13px;margin-top:1px}
  .card--brand .lockup__tag{font-size:19px;letter-spacing:2px;margin-top:5px;color:var(--light-grey)}

  .services{position:absolute;left:0;width:100%;top:330px;text-align:center;color:var(--red);font-size:16px;font-weight:700;letter-spacing:.5px}
</style>
</head>
<body>

<section class="card card--contact">
  <div class="band band--top"><span class="c-grey"></span><span class="c-dark"></span><span class="c-red"></span></div>

  <div class="person">
    <h1 class="person__name"><b>DARIO</b> WHITCOMBE</h1>
    <p class="person__role">PRINCIPAL</p>
  </div>

  <ul class="contacts">
    <li>
      <svg viewBox="0 0 18 18" aria-hidden="true"><circle cx="9" cy="9" r="8.5" fill="var(--grey)"/><rect x="4.5" y="6" width="9" height="6.5" fill="none" stroke="#fff" stroke-width="1.3"/><path d="M4.5 6 9 9.8 13.5 6" fill="none" stroke="#fff" stroke-width="1.3"/></svg>
      info@dariowhitcombe.com
    </li>
    <li>
      <svg viewBox="0 0 18 18" aria-hidden="true"><circle cx="9" cy="9" r="8.5" fill="var(--grey)"/><path d="M6 4.5c.6 0 1.6 2 1.6 2.4 0 .5-.9.9-.9 1.4 0 .8 2.2 3 3 3 .5 0 .9-.9 1.4-.9.4 0 2.4 1 2.4 1.6 0 .9-1.2 1.6-2 1.6C9 13.6 4.4 9 4.4 6.5c0-.8.7-2 1.6-2z" fill="#fff"/></svg>
      +111 2222 1111
    </li>
    <li>
      <svg viewBox="0 0 18 18" aria-hidden="true"><circle cx="9" cy="9" r="8.5" fill="var(--grey)"/><path d="M9 3.8a3.3 3.3 0 0 0-3.3 3.3C5.7 9.6 9 13.6 9 13.6s3.3-4 3.3-6.5A3.3 3.3 0 0 0 9 3.8z" fill="#fff"/><circle cx="9" cy="7.1" r="1.2" fill="var(--grey)"/></svg>
      Your Address Here 12354
    </li>
  </ul>

  <div class="divider"></div>

  <div class="lockup">
    <span class="lockup__mark"></span>
    <p class="lockup__name">DARIO WHITCOMBE, CPA LLC</p>
    <p class="lockup__tag">CERTIFIED PUBLIC ACCOUNTANT</p>
  </div>

  <p class="services">ACCOUNTING, TAX &amp; CONSULTING SERVICES</p>

  <div class="band band--bottom"><span class="c-grey"></span><span class="c-dark"></span><span class="c-red"></span></div>
</section>

<section class="card card--brand">
  <div class="band band--top"><span class="c-red"></span><span class="c-dark"></span><span class="c-grey"></span></div>

  <div class="lockup">
    <span class="lockup__mark"></span>
    <p class="lockup__name">DARIO WHITCOMBE, CPA LLC</p>
    <p class="lockup__tag">CERTIFIED PUBLIC ACCOUNTANT</p>
  </div>

  <div class="band band--bottom"><span class="c-red"></span><span class="c-dark"></span><span class="c-grey"></span></div>
</section>

</body>
</html>
```